African homeware retailer needs a web page design

We need a web page design for a new homeware and accessories store based in Johannesburg, South Africa. Our store carries modern African inspired items from designers that support social development and poverty alleviation initiatives. We have a particular preference for outfits that are centred on the empowerment of women.

Our business celebrates the skill, design and product of African craft and the work of designers looking to take that forward in a socially beneficial way (creating employment, developing skills, supporting local crafts people etc). We aim to carry items and inspirations from all over the African continent.

We would like to see a design that communicates African beauty and elegance without the typical tribal references that are made in reference to African craft or art.

We would like the web page to be stylish, uncomplicated, modern, captivating and appealing to the discerning customer. A similar value proposition is that of http://www.marlowtenwick.example/.

This is an e-commerce website which must be attractive to both individual buyers and design professionals so the website needs to look professional.

Here are links to some websites we like:
http://www.quenbyhollis.example/
http://www.dravelo.example/

Our logo is attached to the brief.

Target Market(s)

Our target market is female, age 20-50. However should not alienate the design conscious male customer therefore

Industry/Entity Type

E-Commerce

Requirements
Must have
• - A featured product banner which includes a photograph and text. This should be easy to edit as we will be changing the featured product regularly
- An easily expendable products section with categories. Examples of categories could be cushions, bedding, crockery etc. Should be easy to add new categories as well as new product pictures
- Home/landing page should be uncluttered
- Should use the logo and should be easy to change the logo which we have in various colour combinations. We plan to change the logo colours depending on circumstance e.g. make it red and white around Valentines day (similar to the way Vintrel frequently changes the logo on their landing page)

```html
<!DOCTYPE html>
<html lang="en">
<head>
<meta charset="utf-8">
<title>Amani Habitat — homeware &amp; accessories</title>
<link href="https://fonts.googleapis.com/css2?family=Ubuntu:wght@400;500;700&family=Lora:ital,wght@1,400;1,700&display=swap" rel="stylesheet">
<style>
:root{
  --cream:#f6efc6;
  --navy:#1d4a62;
  --green:#2f9a2c;
  --green-dark:#1f7a1d;
  --teal-logo:#1e6e6a;
  --text:#3d3d3d;
  --footer:#343434;
  --footer-dark:#2a2a2a;
  --white:#ffffff;
}
*{box-sizing:border-box;margin:0;padding:0}
html,body{width:900px;height:1200px;overflow:hidden}
body{position:relative;font-family:'Ubuntu',sans-serif;color:var(--text);background:var(--white)}
.abs{position:absolute}
.top-rule{left:0;top:0;width:900px;height:3px;background:var(--green)}
.cream-zone{left:0;top:3px;width:900px;height:610px;background:var(--cream)}
.side-band{left:0;top:140px;width:900px;height:257px;background:linear-gradient(90deg,#f3eef0 0%,#ffffff 20%,#ffffff 80%,#eef4f3 100%)}
.brand-mark{left:136px;top:36px;width:56px;height:56px;background:var(--teal-logo)}
.brand-name{left:204px;top:48px;font-size:26px;font-weight:500;color:var(--teal-logo);letter-spacing:1px;line-height:30px;white-space:nowrap}
.brand-tag{left:262px;top:92px;font-size:10px;color:var(--navy);letter-spacing:.5px;white-space:nowrap}
.account{left:588px;top:32px;font-size:11px;color:var(--navy)}
.cart{left:676px;top:29px;font-size:11px;color:var(--green);display:flex;align-items:center;gap:6px}
.phone{left:652px;top:62px;width:120px;display:flex;justify-content:space-between;align-items:center;font-size:13px;font-weight:700;color:var(--green)}
.search{left:625px;top:87px;width:146px;height:18px;background:var(--white);border:1px solid #d9d4b8;font-size:9px;color:#aaa;padding:3px 6px}
.search svg{position:absolute;right:4px;top:3px}
.main-nav{left:129px;top:123px;width:642px;height:32px;background:var(--navy);display:flex;align-items:center}
.main-nav a{color:var(--white);text-decoration:none;font-size:11px;text-align:center;border-right:1px solid #3d6a82;line-height:16px}
.main-nav a:last-child{border-right:none}
.hero{left:129px;top:155px;width:642px;height:290px;overflow:hidden;box-shadow:0 6px 8px rgba(0,0,0,.25)}
.hero-photo{position:absolute;inset:0;background:linear-gradient(90deg,#d8d2cc 0%,#c9bcb0 30%,#6b4e3c 45%,#2a2a2c 60%,#3a2c30 100%)}
.hero-copy{position:absolute;left:0;top:0;width:290px;height:290px;background:rgba(235,232,228,.55)}
.hero-kicker{position:absolute;left:37px;top:50px;font-size:19px;font-weight:500;color:#5a5a5a;white-space:nowrap}
.hero-title{position:absolute;left:37px;top:73px;font-size:25px;font-weight:500;color:#1a1a1a;white-space:nowrap}
.hero-text{position:absolute;left:40px;top:104px;width:205px;font-size:10px;line-height:12px;color:#555}
.btn{background:linear-gradient(#3aa836,var(--green-dark));color:var(--white);font-weight:700;font-size:12px;text-align:center;border-radius:2px;box-shadow:0 1px 2px rgba(0,0,0,.3)}
.hero-btn{position:absolute;left:38px;top:185px;width:155px;height:30px;line-height:30px}
.slide-arrow{top:268px;width:28px;height:28px;background:var(--navy)}
.intro-title{left:0;top:480px;width:900px;text-align:center;font-size:19px;font-weight:500;color:#2b2b2b}
.intro-text{left:144px;top:511px;width:614px;font-size:9px;line-height:13px;color:#444}
.intro-btn{left:405px;top:562px;width:90px;height:31px;line-height:31px}
.sidebar{left:129px;top:634px;width:171px;height:343px;background:var(--navy);border-radius:2px;color:var(--white)}
.sidebar h2{position:absolute;left:12px;top:15px;font-size:16px;font-weight:500}
.cat-list{position:absolute;left:8px;top:54px;width:157px;list-style:none}
.cat-list li{font-size:9.5px;height:19.8px;line-height:19.8px;border-bottom:1px solid #2e5d75;padding-left:12px;position:relative;white-space:nowrap}
.cat-list li::before{content:"";position:absolute;left:2px;top:8px;border-left:4px solid #cfdde4;border-top:2.5px solid transparent;border-bottom:2.5px solid transparent}
.ship{position:absolute;left:0;width:171px;text-align:center}
.ship-title{top:259px;font-size:15px;font-weight:500}
.ship-amount{top:297px;font-size:12px;font-weight:500}
.ship-note{top:315px;font-size:9px}
.product{width:141px;height:107px;background:var(--white);border-radius:3px;overflow:hidden;box-shadow:0 1px 2px rgba(0,0,0,.2)}
.product-label{position:absolute;left:0;top:0;width:141px;height:17px;background:var(--green);color:var(--white);font-size:9px;font-weight:700;line-height:17px;padding-left:19px}
.product-label::before{content:"";position:absolute;left:7px;top:5px;width:6px;height:6px;background:#e6d84a;border-radius:1px}
.product-photo{position:absolute;left:0;top:17px;width:141px;height:90px}
.product-foot{position:absolute;left:0;bottom:0}
.product-detail{position:absolute;right:6px;bottom:3px;font-size:9px;font-weight:700;color:var(--white)}
.footer{left:0;top:1000px;width:900px;height:200px;background:var(--footer)}
.foot-h{top:1022px;font-size:13px;font-weight:700;color:var(--white)}
.quote{left:131px;top:1052px;width:234px;height:76px;background:var(--footer-dark);border-radius:8px;padding:16px 18px;font-family:'Lora',serif;font-size:9px;line-height:11px;color:#6a6a6a;font-style:normal}
.quote-tail{left:310px;top:1126px}
.avatar{left:146px;top:1138px;width:33px;height:33px;border-radius:50%;background:linear-gradient(#c9ced4,#8d939a);border:2px solid #eee}
.quote-name{left:191px;top:1141px;font-family:'Lora',serif;font-style:italic;font-weight:700;font-size:11px;color:var(--white)}
.quote-role{left:191px;top:1157px;font-family:'Lora',serif;font-style:italic;font-weight:700;font-size:9px;color:#ddd}
.contact-row{left:401px;display:flex;gap:9px;font-size:10px;color:var(--white);line-height:13px}
.card-badge{top:1155px;width:26px;height:16px;border-radius:2px}
.news-text{left:605px;top:1048px;font-size:9px;line-height:12px;color:var(--white);width:160px}
.news-input{left:605px;top:1076px;width:163px;height:20px;background:var(--white);font-size:9px;color:#888;padding:4px 6px}
.social{top:1111px;width:18px;height:18px;border-radius:50%;background:var(--green)}
.subscribe{left:704px;top:1108px;width:64px;height:20px;line-height:20px;font-weight:500;font-size:10px}
.copyright{left:615px;top:1160px;font-size:9px;color:#ddd}
</style>
</head>
<body>
<div class="abs top-rule"></div>
<div class="abs cream-zone"></div>
<div class="abs side-band"></div>

<header>
  <div class="abs brand-mark"></div>
  <div class="abs brand-name">AMANI HABITAT</div>
  <div class="abs brand-tag">homeware &amp; accessories</div>
  <div class="abs account">Login | Register</div>
  <div class="abs cart">
    <svg width="20" height="16" viewBox="0 0 20 16"><path d="M1 2h3l2 9h10l2-7H5" fill="none" stroke="#2f9a2c" stroke-width="1.6"/><circle cx="8" cy="14" r="1.5" fill="#2f9a2c"/><circle cx="15" cy="14" r="1.5" fill="#2f9a2c"/></svg>
    <span>Cart <span style="color:var(--navy)">(0 item)</span> ▾</span>
  </div>
  <div class="abs phone">
    <svg width="16" height="16" viewBox="0 0 16 16"><circle cx="8" cy="8" r="7" fill="none" stroke="#1d4a62" stroke-width="1.6"/><path d="M5.5 4.5l1.5 1.5-1 1c.5 1.2 1.3 2 2.5 2.5l1-1 1.5 1.5-1 1c-2.5-.3-4.5-2.3-4.8-4.8z" fill="#1d4a62"/></svg>
    <span>41 55 07 318</span>
  </div>
  <div class="abs search">Search
    <svg width="11" height="11" viewBox="0 0 11 11"><circle cx="4.5" cy="4.5" r="3.5" fill="none" stroke="#222" stroke-width="1.5"/><path d="M7 7l3 3" stroke="#222" stroke-width="1.6"/></svg>
  </div>
  <nav class="abs main-nav">
    <a style="width:88px">Home</a><a style="width:91px">About Us</a><a style="width:82px">Services</a><a style="width:88px">Products</a><a style="width:66px">FAQ</a><a style="width:116px">Order Tracking</a><a style="width:111px">Contact Us</a>
  </nav>
</header>

<section class="abs hero">
  <div class="hero-photo" role="img" aria-label="Featured photo of colourful beaded bowls, woven baskets, cushions and a painted vase on a dark table"></div>
  <div class="hero-copy"></div>
  <div class="hero-kicker">Exclusive Collection of</div>
  <div class="hero-title">Home Accessories</div>
  <p class="hero-text">Aenean sem velit, aliquet ut feugiat nec, pla cerat quis odio. Curabitur fringilla imperdiet justo</p>
  <div class="btn hero-btn">Click here to view more</div>
</section>
<svg class="abs slide-arrow" style="left:120px" viewBox="0 0 28 28"><rect width="28" height="28" fill="#1d4a62"/><path d="M17 8l-6 6 6 6" fill="none" stroke="#fff" stroke-width="2.5"/></svg>
<svg class="abs slide-arrow" style="left:754px" viewBox="0 0 28 28"><rect width="28" height="28" fill="#1d4a62"/><path d="M11 8l6 6-6 6" fill="none" stroke="#fff" stroke-width="2.5"/></svg>

<h1 class="abs intro-title">Mauris vitae enim velit. Proin id lorem nec massa auctor</h1>
<p class="abs intro-text">Aenean sem velit, aliquet ut feugiat nec, placerat quis odio. Curabitur fringilla imperdiet justo, vel rutrum elit pharetra at. Nam scelerisque dui eros. Pellentesque ac euismod turpis. Cras lacinia dui leo, ac imperdiet risus tincidunt id. Praesent leo urna, interdum sit amet tortor lobortis, tempor facilisis ligula. Aliquam in egestas urna. Curabitur lacinia velit a libero tincidunt interdum. Maecenas aliquet mauris id leo rhoncus, sed eleifend enim feugiat.</p>
<div class="abs btn intro-btn">View more</div>

<aside class="abs sidebar">
  <h2>Pruduct Catagories</h2>
  <ul class="cat-list">
    <li>Duis interdum neque vitae lorem</li>
    <li>Condimentum imperdiet.</li>
    <li>Fusce congue ultricies purus.</li>
    <li>Sed interdum nisi vestibulum</li>
    <li>Dapibus dignissim Nulla ac tellus</li>
    <li>Lacus bibendum</li>
    <li>DignissimCurabitur dictum</li>
    <li>Eleifend felis eu ornare Nulla</li>
    <li>Integer malesuada blandit tristi</li>
  </ul>
  <div class="ship ship-title">Free Shipping</div>
  <div class="ship ship-amount">Order over $200</div>
  <div class="ship ship-note">Not Valid for International Order</div>
</aside>

<section class="product-grid">
  <div class="abs product" style="left:331px;top:638px"><div class="product-photo" role="img" aria-label="Woven fruit basket in grey, yellow and white stripes" style="background:linear-gradient(#c9c4a8,#9c9a8e)"></div><div class="product-label">Fruit Basket</div><svg class="product-foot" width="141" height="32" viewBox="0 0 141 32"><path d="M0 14 Q70 -6 141 14 V32 H0Z" fill="#fff"/><path d="M0 18 Q70 0 141 18 V32 H0Z" fill="#1d4a62"/></svg><span class="product-detail">Detail</span></div>
  <div class="abs product" style="left:480px;top:638px"><div class="product-photo" role="img" aria-label="Red glazed rinket box with tree silhouette" style="background:radial-gradient(circle at 50% 50%,#d8321f,#5a0c08)"></div><div class="product-label">Rinket Box</div><svg class="product-foot" width="141" height="32" viewBox="0 0 141 32"><path d="M0 14 Q70 -6 141 14 V32 H0Z" fill="#fff"/><path d="M0 18 Q70 0 141 18 V32 H0Z" fill="#1d4a62"/></svg><span class="product-detail">Detail</span></div>
  <div class="abs product" style="left:629px;top:638px"><div class="product-photo" role="img" aria-label="Red tray with white vase and flower" style="background:linear-gradient(#efebe8,#dcd4d0)"></div><div class="product-label">Nabo Tray</div><svg class="product-foot" width="141" height="32" viewBox="0 0 141 32"><path d="M0 14 Q70 -6 141 14 V32 H0Z" fill="#fff"/><path d="M0 18 Q70 0 141 18 V32 H0Z" fill="#1d4a62"/></svg><span class="product-detail">Detail</span></div>
  <div class="abs product" style="left:331px;top:754px"><div class="product-photo" role="img" aria-label="Printed brown and gold fabric cushion" style="background:linear-gradient(135deg,#9bc98a,#8a4a22 40%,#6a3418)"></div><div class="product-label">Fruit Basket</div><svg class="product-foot" width="141" height="32" viewBox="0 0 141 32"><path d="M0 14 Q70 -6 141 14 V32 H0Z" fill="#fff"/><path d="M0 18 Q70 0 141 18 V32 H0Z" fill="#1d4a62"/></svg><span class="product-detail">Detail</span></div>
  <div class="abs product" style="left:480px;top:754px"><div class="product-photo" role="img" aria-label="Seed bead necklace hanging over a white lamp" style="background:linear-gradient(#f2f0ec,#cfc8bf)"></div><div class="product-label">Seed Bead</div><svg class="product-foot" width="141" height="32" viewBox="0 0 141 32"><path d="M0 14 Q70 -6 141 14 V32 H0Z" fill="#fff"/><path d="M0 18 Q70 0 141 18 V32 H0Z" fill="#1d4a62"/></svg><span class="product-detail">Detail</span></div>
  <div class="abs product" style="left:629px;top:754px"><div class="product-photo" role="img" aria-label="Set of pink patterned drawer knobs" style="background:linear-gradient(#c8b8b0,#9c8e88)"></div><div class="product-label">Nabo Tray</div><svg class="product-foot" width="141" height="32" viewBox="0 0 141 32"><path d="M0 14 Q70 -6 141 14 V32 H0Z" fill="#fff"/><path d="M0 18 Q70 0 141 18 V32 H0Z" fill="#1d4a62"/></svg><span class="product-detail">Detail</span></div>
  <div class="abs product" style="left:331px;top:870px"><div class="product-photo" role="img" aria-label="Shell disc bracelet in cream and brown tones" style="background:linear-gradient(135deg,#e0cfae,#a87e52)"></div><div class="product-label">Fruit Basket</div><svg class="product-foot" width="141" height="32" viewBox="0 0 141 32"><path d="M0 14 Q70 -6 141 14 V32 H0Z" fill="#fff"/><path d="M0 18 Q70 0 141 18 V32 H0Z" fill="#1d4a62"/></svg><span class="product-detail">Detail</span></div>
  <div class="abs product" style="left:480px;top:870px"><div class="product-photo" role="img" aria-label="Woven wire basket in red, blue and yellow stripes" style="background:linear-gradient(160deg,#c83a2a,#3a6aa8 50%,#d8b030)"></div><div class="product-label">Rinket Box</div><svg class="product-foot" width="141" height="32" viewBox="0 0 141 32"><path d="M0 14 Q70 -6 141 14 V32 H0Z" fill="#fff"/><path d="M0 18 Q70 0 141 18 V32 H0Z" fill="#1d4a62"/></svg><span class="product-detail">Detail</span></div>
  <div class="abs product" style="left:629px;top:870px"><div class="product-photo" role="img" aria-label="Green gemstone beaded bracelet" style="background:linear-gradient(#e6e6e4,#c4c8bc)"></div><div class="product-label">Gymstone</div><svg class="product-foot" width="141" height="32" viewBox="0 0 141 32"><path d="M0 14 Q70 -6 141 14 V32 H0Z" fill="#fff"/><path d="M0 18 Q70 0 141 18 V32 H0Z" fill="#1d4a62"/></svg><span class="product-detail">Detail</span></div>
</section>

<footer>
  <div class="abs footer"></div>
  <h3 class="abs foot-h" style="left:135px">Testimonials</h3>
  <blockquote class="abs quote">Curabitur quis vestibulum nulla. Phasellus nisi mauris, fermentum vitae eros in, volutpat sollicitudin erat. Vestibulum consectetur enim in ultrices hendrerit.</blockquote>
  <svg class="abs quote-tail" width="24" height="20" viewBox="0 0 24 20"><path d="M0 0h24L10 20z" fill="#2a2a2a"/></svg>
  <div class="abs avatar" role="img" aria-label="Customer portrait"></div>
  <div class="abs quote-name">Aliquam egestas</div>
  <div class="abs quote-role">imperdiet dictum lacus</div>

  <h3 class="abs foot-h" style="left:399px">Contact Info</h3>
  <div class="abs contact-row" style="top:1050px"><svg width="11" height="11" viewBox="0 0 11 11"><path d="M5.5 1L1 5h1.5v5h6V5H10z" fill="#fff"/></svg><span style="width:150px">Fusce porta leo 345 egestas sagittis. Integer ut ante</span></div>
  <div class="abs contact-row" style="top:1083px"><svg width="11" height="11" viewBox="0 0 11 11"><path d="M2 1l2 2-1 1.5c.8 1.5 2 2.7 3.5 3.5L8 7l2 2-1.5 1.5C5 10 1 6 .5 2.5z" fill="#fff"/></svg><span>418 552 0710</span></div>
  <div class="abs contact-row" style="top:1104px"><svg width="11" height="11" viewBox="0 0 11 11"><rect x="2.5" y="1" width="6" height="3" fill="#fff"/><rect x="0.5" y="4" width="10" height="4" fill="#fff"/><rect x="2.5" y="7" width="6" height="3.5" fill="#fff" stroke="#343434"/></svg><span>418 552 0722</span></div>
  <div class="abs contact-row" style="top:1125px"><svg width="11" height="11" viewBox="0 0 11 11"><rect x="0.5" y="2" width="10" height="7" fill="#fff"/><path d="M0.5 2l5 4 5-4" fill="none" stroke="#343434"/></svg><span>info@amanihabitat.example</span></div>
  <div class="abs card-badge" style="left:401px;background:#f2f2f2"></div>
  <div class="abs card-badge" style="left:433px;background:#e6e6e6"></div>
  <div class="abs card-badge" style="left:465px;background:#3a7bc0"></div>
  <div class="abs card-badge" style="left:497px;background:#1a3a6a"></div>

  <h3 class="abs foot-h" style="left:600px">Subscribe Newsletter</h3>
  <p class="abs news-text">Enter you email to get our monthly News updates</p>
  <div class="abs news-input">Enter Email address
    <svg style="position:absolute;right:6px;top:5px" width="12" height="9" viewBox="0 0 12 9"><rect x=".5" y=".5" width="11" height="8" fill="#ccc"/><path d="M.5 .5l5.5 4 5.5-4" fill="none" stroke="#888"/></svg>
  </div>
  <div class="abs social" style="left:603px"></div>
  <div class="abs social" style="left:624px"></div>
  <div class="abs social" style="left:647px"></div>
  <div class="abs social" style="left:671px"></div>
  <div class="abs btn subscribe">Subscribe</div>
  <div class="abs copyright">Copyright © 2014 , all rights reserved.</div>
</footer>
</body>
</html>
```